Business Card Design for Occupational Medicine Start Up Company

We need to design a professional business card. We are a healthcare company providing occupational medicine services to blue collar industries. We are professional, efficient and high quality service providers.

Target Market(s)

Blue Collar Industry: Shipbuilding, Ports, Trucking Companies; The Executives and Safety Officers for these companies

Industry/Entity Type

Healthcare

Contact Information for Business Card

Logo, Name, Title, Email, Phone

Other font styles liked:
• Please match our Brand Guide

Requirements
Must have
• Our Company Colors and Logo

```html
<!DOCTYPE html>
<html lang="en">
<head>
<meta charset="utf-8">
<title>CrewWell Clinics Business Card</title>
<link href="https://fonts.googleapis.com/css2?family=Montserrat:wght@400;500;700&display=swap" rel="stylesheet">
<style>
  :root {
    --backdrop: #2b2b2b;
    --paper: #f6f6f4;
    --navy: #2e2f7a;
    --sky: #2b9bd6;
    --gold: #e8a93a;
    --ink-soft: #3a3b7e;
  }
  * { margin: 0; padding: 0; box-sizing: border-box; }
  html, body {
    width: 1200px; height: 1200px; overflow: hidden;
    background: var(--backdrop);
    font-family: "Montserrat", sans-serif;
  }
  .canvas { position: relative; width: 1200px; height: 1200px; }
  .card {
    position: absolute; left: 300px; width: 594px; height: 348px;
    background: var(--paper); border-radius: 24px; overflow: hidden;
  }
  .card--front { top: 200px; }
  .card--back { top: 637px; }

  .brand { position: absolute; text-align: center; color: var(--navy); font-weight: 700; }
  .brand__dot {
    display: block; margin: 0 auto 14px; border-radius: 50%; background: var(--navy);
  }
  .brand__name { display: block; letter-spacing: 0.5px; line-height: 1; }
  .brand__sub { display: block; letter-spacing: 5px; line-height: 1; margin-top: 6px; }

  .card--front .brand { left: 0; right: 0; top: 98px; }
  .card--front .brand__dot { width: 64px; height: 64px; }
  .card--front .brand__name { font-size: 38px; }
  .card--front .brand__sub { font-size: 19px; }

  .front__web {
    position: absolute; left: 0; right: 0; top: 500px; top: 300px;
    text-align: center; font-size: 16px; letter-spacing: 1px; color: var(--navy);
  }

  .card--back .brand { left: 40px; width: 250px; top: 82px; }
  .card--back .brand__dot { width: 56px; height: 56px; }
  .card--back .brand__name { font-size: 28px; }
  .card--back .brand__sub { font-size: 15px; letter-spacing: 4px; }

  .person { position: absolute; left: 316px; top: 62px; }
  .person__name { font-size: 25px; font-weight: 500; color: var(--sky); letter-spacing: 0.5px; }
  .person__title { font-size: 15px; color: var(--navy); margin-top: 2px; }

  .contacts { position: absolute; left: 316px; top: 128px; list-style: none; }
  .contacts li {
    display: flex; align-items: center; gap: 12px;
    font-size: 15.5px; color: var(--navy); height: 21.5px;
  }
  .contacts svg { width: 14px; height: 14px; flex: none; }
  .address { position: absolute; left: 316px; top: 208px; display: flex; gap: 12px; }
  .address svg { width: 14px; height: 16px; margin-top: 2px; }
  .address p { font-size: 15.5px; color: var(--navy); line-height: 22px; }

  .back__band { position: absolute; left: 0; bottom: 0; width: 594px; height: 44px; }
  .back__specialty {
    position: absolute; right: 70px; bottom: 10px;
    font-size: 15.5px; color: #ffffff;
  }
</style>
</head>
<body>
<main class="canvas">
  <section class="card card--front" aria-label="Card front">
    <div class="brand">
      <span class="brand__dot"></span>
      <span class="brand__name">CREWWELL</span>
      <span class="brand__sub">CLINICS</span>
    </div>
    <p class="front__web">www.crewwellclinics.com</p>
  </section>

  <section class="card card--back" aria-label="Card back">
    <div class="brand">
      <span class="brand__dot"></span>
      <span class="brand__name">CREWWELL</span>
      <span class="brand__sub">CLINICS</span>
    </div>

    <div class="person">
      <h1 class="person__name">DANIEL REYES</h1>
      <p class="person__title">Senior Doctor</p>
    </div>

    <ul class="contacts">
      <li>
        <svg viewBox="0 0 14 14" aria-hidden="true"><path d="M2 5c0-2 2-3 5-3s5 1 5 3v1h-3V5H5v1H2z M3 7h8l1 5H2z" fill="var(--sky)"/></svg>
        555-014-2290
      </li>
      <li>
        <svg viewBox="0 0 14 14" aria-hidden="true"><rect x="1" y="3" width="12" height="8" fill="var(--navy)"/><path d="M1 3l6 5 6-5" stroke="#fff" stroke-width="1.2" fill="none"/></svg>
        hello@crewwell.com
      </li>
      <li>
        <svg viewBox="0 0 14 14" aria-hidden="true"><circle cx="7" cy="7" r="5.5" fill="none" stroke="var(--gold)" stroke-width="1.4"/><path d="M1.5 7h11M7 1.5c-3 3-3 8 0 11M7 1.5c3 3 3 8 0 11" stroke="var(--gold)" stroke-width="1.1" fill="none"/></svg>
        www.crewwell.com
      </li>
    </ul>

    <div class="address">
      <svg viewBox="0 0 14 16" aria-hidden="true"><path d="M7 1a5 5 0 0 1 5 5c0 4-5 9-5 9S2 10 2 6a5 5 0 0 1 5-5z" fill="var(--gold)"/><circle cx="7" cy="6" r="2" fill="var(--paper)"/></svg>
      <p>48 Harbor Avenue, Suite 210<br>Port Landing, State 20415</p>
    </div>

    <svg class="back__band" viewBox="0 0 594 44" aria-hidden="true">
      <rect x="0" y="18" width="270" height="4" fill="var(--sky)"/>
      <rect x="0" y="26" width="266" height="4" fill="var(--navy)"/>
      <rect x="0" y="37" width="260" height="4" fill="var(--gold)"/>
      <path d="M290 0H594V44H262L274 10Q278 0 290 0z" fill="var(--navy)"/>
    </svg>
    <p class="back__specialty">Occupational Medicine</p>
  </section>
</main>
</body>
</html>
```